Business card design

We need a business card designed completed for a new company. We are a company that works with associations, schools to convert their older text/DVDs into dynamic online and mobile programs. Our initial platform is designed for the legal associations and will enable their lawyers to access their content such as forms, videos, case law and support materials anywhere, anytime. We are also focused on Project Management Associations, Financial Management Associations and IT Associations.

I would like for the business card to have the following information:

Logo

Kent marrowby

President and CEO

kmarrowby@trevantiq.example

Mobile: 555-374-9160

www.trevantiq.example

Tag line: Transforming content into a mobile platform    

I would like it to be double sided, use the colours of the logo, tie into the mobile world

 

Industry/Entity Type

Legal

Logo Text

Trevantiq

```html
<!DOCTYPE html>
<html lang="en">
<head>
<meta charset="utf-8">
<title>Trevantiq business card set</title>
<link rel="stylesheet" href="https://fonts.googleapis.com/css2?family=Source+Sans+3:wght@400;600;700&display=swap">
<style>
  :root {
    --stage: #a8825e;
    --label: #2a1a10;
    --card-grey: #999999;
    --card-white: #ffffff;
    --wave-dark: #666666;
    --wave-light: #b4b4b4;
    --wave-accent: #4a1a10;
    --ink-dark: #222222;
    --ink-light: #ffffff;
    --logo-on-white: #666666;
  }
  * { box-sizing: border-box; margin: 0; padding: 0; }
  html, body { width: 1200px; height: 800px; overflow: hidden; }
  body {
    background: var(--stage);
    font-family: "Source Sans 3", "Myriad Pro", Arial, sans-serif;
    position: relative;
  }
  .view-label {
    position: absolute;
    width: 510px;
    text-align: center;
    font-size: 21px;
    color: var(--label);
  }
  .card {
    position: absolute;
    width: 510px;
    height: 290px;
    border-radius: 20px;
    overflow: hidden;
  }
  .card--grey { background: var(--card-grey); }
  .card--white { background: var(--card-white); }
  .card__wave { position: absolute; inset: 0; width: 100%; height: 100%; }
  .brand-name {
    position: absolute;
    font-weight: 700;
    line-height: 1;
    letter-spacing: -1px;
  }
  .card--grey .brand-name { color: var(--ink-light); }
  .card--white .brand-name { color: var(--logo-on-white); }
  .brand-name--small { left: 36px; top: 46px; font-size: 60px; }
  .brand-name--large { left: 0; right: 0; top: 100px; text-align: center; font-size: 84px; }
  .person { position: absolute; left: 36px; top: 158px; font-size: 16px; color: var(--ink-dark); }
  .person__role { font-size: 13px; }
  .phone { position: absolute; left: 36px; top: 190px; font-size: 13px; color: var(--ink-dark); }
  .contact-key { font-weight: 700; font-style: italic; }
  .tagline {
    position: absolute; right: 22px; top: 192px;
    text-align: right; font-size: 15.5px; line-height: 20px; color: var(--ink-light);
  }
  .contact-lines {
    position: absolute; right: 22px; top: 240px;
    text-align: right; font-size: 13.5px; line-height: 19px; color: var(--ink-light);
  }
  .web-line {
    position: absolute; left: 0; right: 0; bottom: 18px;
    text-align: center; font-size: 15px; letter-spacing: 3px; color: var(--ink-dark);
  }
</style>
</head>
<body>

<p class="view-label" style="left:80px;top:50px;">Front</p>
<p class="view-label" style="left:632px;top:50px;">Back - 1</p>
<p class="view-label" style="left:73px;top:410px;">Back - 2</p>
<p class="view-label" style="left:634px;top:410px;">Back - 3</p>

<!-- Front -->
<section class="card card--grey" style="left:80px;top:97px;">
  <svg class="card__wave" viewBox="0 0 510 290" preserveAspectRatio="none" aria-hidden="true">
    <path d="M0,222 C120,265 240,250 330,180 C400,125 460,105 510,98 L510,290 L0,290 Z" fill="var(--wave-dark)"/>
    <path d="M0,218 C120,255 240,238 330,168 C400,115 460,96 510,88" fill="none" stroke="var(--wave-light)" stroke-width="7"/>
    <path d="M0,240 C80,268 170,266 240,238" fill="none" stroke="var(--wave-accent)" stroke-width="6"/>
    <path d="M0,250 C90,276 180,272 250,245" fill="none" stroke="var(--wave-light)" stroke-width="3"/>
  </svg>
  <p class="brand-name brand-name--small">Trevantiq</p>
  <p class="person">Kent marrowby, <span class="person__role">President and CEO</span></p>
  <p class="phone"><span class="contact-key">c</span> : 555-374-9160</p>
  <p class="tagline">Transforming content<br>into a mobile platform</p>
  <p class="contact-lines"><span class="contact-key">e</span> : kmarrowby@trevantiq.example<br><span class="contact-key">w</span> : www.trevantiq.example</p>
</section>

<!-- Back 1 -->
<section class="card card--white" style="left:632px;top:97px;">
  <svg class="card__wave" viewBox="0 0 510 290" preserveAspectRatio="none" aria-hidden="true">
    <path d="M0,222 C120,265 240,250 330,180 C400,125 460,105 510,98 L510,290 L0,290 Z" fill="var(--wave-dark)"/>
    <path d="M0,218 C120,255 240,238 330,168 C400,115 460,96 510,88" fill="none" stroke="var(--wave-light)" stroke-width="7"/>
    <path d="M0,240 C80,268 170,266 240,238" fill="none" stroke="var(--wave-accent)" stroke-width="6"/>
    <path d="M0,250 C90,276 180,272 250,245" fill="none" stroke="var(--card-white)" stroke-width="3"/>
  </svg>
  <p class="brand-name brand-name--small">Trevantiq</p>
  <p class="person">Kent marrowby, <span class="person__role">President and CEO</span></p>
  <p class="phone"><span class="contact-key">c</span> : 555-374-9160</p>
  <p class="tagline">Transforming content<br>into a mobile platform</p>
  <p class="contact-lines"><span class="contact-key">e</span> : kmarrowby@trevantiq.example<br><span class="contact-key">w</span> : www.trevantiq.example</p>
</section>

<!-- Back 2 -->
<section class="card card--grey" style="left:73px;top:452px;">
  <p class="brand-name brand-name--large">Trevantiq</p>
  <p class="web-line">www.trevantiq.example</p>
</section>

<!-- Back 3 -->
<section class="card card--white" style="left:634px;top:450px;">
  <p class="brand-name brand-name--large">Trevantiq</p>
  <p class="web-line">www.trevantiq.example</p>
</section>

</body>
</html>
```